Pebblebrook Plots - Online-only garden installation company

Online-only garden installation company. Our demographic is middle aged / suburban women, and we anticipate Facebook driving traffic to this website, as well as referrals from garden centers. The website must be very simple in design and function.

All orders will be placed through the website, including size of garden (3 options), location in yard, payment, and scheduling of installation date.

The website should employ a 3 step process:

Step 1: Select garden size. Either an 4' X 4', 8' X 4', or 12' X 4'.

Step 2: Select a location. We would like to use online maps to look up a US address, then "drag and drop" one of the garden sizes from step 1 to the location the customer would like us to install the garden at their home.

Step 3: Pick an installation date and pay. Using an online calendar the customer will pick a date, and then pay for the installation via credit card.

The website will be linked to an email account, PebblebrookPlots@mailvale.com to inform us of orders placed.

Target Market(s)

Our demographic is middle aged / suburban women, and we anticipate Facebook driving traffic to this website, as well as referrals from garden centers.

Industry/Entity Type

Coding

Number of Pages Required

Requirements
Must have
• Scheduling and payment options.

```html
<!DOCTYPE html>
<html lang="en">
<head>
<meta charset="utf-8">
<title>Pebblebrook Plots – Garden Installation</title>
<link href="https://fonts.googleapis.com/css2?family=Open+Sans:ital,wght@0,400;0,600;0,700;1,400&family=Montserrat:wght@600;700&display=swap" rel="stylesheet">
<style>
:root{
  --green:#2f7a36;
  --title-green:#2e7d32;
  --orange:#e4612a;
  --orange-soft:#f0a07a;
  --text:#555;
  --text-dark:#333;
  --gray-bg:#ededed;
  --foot-bar:#f1f1f1;
  --white:#fff;
}
*{box-sizing:border-box;margin:0;padding:0}
html,body{width:1200px;height:3315px;overflow:hidden}
body{position:relative;background:var(--white);font-family:'Open Sans',Arial,sans-serif;color:var(--text)}
.abs{position:absolute}
a{color:inherit;text-decoration:none}

/* header */
.site-header{position:absolute;top:0;left:0;width:1200px;height:88px;background:var(--white);z-index:5}
.nav a{position:absolute;top:34px;font-size:14px;color:var(--text-dark)}
.nav a.active{color:var(--orange)}
.nav .underline{position:absolute;left:116px;top:82px;width:46px;height:4px;background:var(--orange)}
.brand-badge{position:absolute;left:505px;top:-30px;width:190px;height:190px;border-radius:50%;background:var(--white);z-index:6}
.brand-badge span{position:absolute;left:0;top:112px;width:190px;text-align:center;font-weight:700;font-size:16px;line-height:20px;color:var(--green);letter-spacing:.3px}

/* hero */
.hero{position:absolute;top:88px;left:0;width:1200px;height:520px;overflow:hidden}
.hero-photo{position:absolute;inset:0;background:linear-gradient(180deg,#6f8f5a 0%,#a9a08a 30%,#b98a9e 55%,#5d8a3f 80%,#4d7a32 100%)}
.hero h1{position:absolute;left:99px;top:150px;font-size:44px;font-weight:600;color:var(--white)}
.hero p{position:absolute;left:101px;top:212px;font-size:22px;color:var(--white)}
.btn-solid{position:absolute;background:var(--orange);color:var(--white);font-family:'Montserrat',Arial,sans-serif;font-weight:600;font-size:11px;border-radius:22px;display:flex;align-items:center;justify-content:center;text-transform:uppercase}
.hero .btn-solid{left:99px;top:274px;width:201px;height:44px;font-size:12px}
.hero-dots{position:absolute;left:572px;top:482px;display:flex;gap:6px;z-index:2}
.hero-dots i{width:8px;height:8px;border-radius:50%;background:#cfd9c6}
.hero-dots i:first-child{background:var(--orange)}
.hero-wave{position:absolute;left:0;bottom:0}

/* section titles */
.sec-title{position:absolute;left:0;width:1200px;text-align:center;font-size:28px;font-weight:700;color:var(--title-green)}
.sec-lead{position:absolute;text-align:center;font-size:12.5px;line-height:30px;color:var(--text)}

/* steps */
.step{position:absolute;top:824px;width:260px;text-align:center}
.step svg{display:block;margin:0 auto}
.step h3{font-size:14px;font-weight:600;color:var(--text-dark);margin-top:28px}
.step p{font-size:12px;line-height:23px;margin-top:8px;color:var(--text)}

/* feature band */
.band{position:absolute;top:1198px;height:450px;width:600px}
.band.green{left:0;background:var(--green)}
.band.orange{left:600px;background:var(--orange)}
.band h2{position:absolute;left:88px;top:104px;font-size:29px;font-weight:600;color:var(--white)}
.band p{position:absolute;left:88px;top:158px;width:440px;font-size:12px;line-height:27px;color:var(--white)}
.btn-ghost{position:absolute;left:88px;top:252px;width:146px;height:36px;border:1px solid var(--white);border-radius:20px;color:var(--white);font-family:'Montserrat',Arial,sans-serif;font-weight:600;font-size:10px;display:flex;align-items:center;justify-content:center;text-transform:uppercase}
.band-wave{position:absolute;left:0;top:1520px}

/* works */
.work{position:absolute;top:1790px;width:234px}
.work .ph{height:172px;border-radius:10px}
.work h4{margin-top:16px;text-align:center;font-size:12.5px;font-weight:600;color:var(--green);text-transform:uppercase}
.arrow{position:absolute;top:1864px}

/* blog */
.blog{position:absolute;top:2064px;left:0;width:1200px;height:596px;background:var(--gray-bg)}
.post{position:absolute;top:117px;width:312px}
.post .ph{height:204px;border-radius:4px}
.post h4{margin-top:18px;font-size:13px;font-weight:700;line-height:20px;color:var(--text-dark)}
.post p{margin-top:12px;font-size:12px;line-height:22px;color:var(--text)}
.post .btn-solid{position:relative;margin-top:18px;width:124px;height:36px}

/* testimonial */
.testimonial{position:absolute;top:2659px;left:0;width:1200px;height:372px}
.testimonial .quote-mark{position:absolute;left:580px;top:76px}
.testimonial blockquote{position:absolute;left:180px;top:130px;width:840px;text-align:center;font-style:italic;font-size:13px;line-height:34px;color:var(--white)}
.avatar{position:absolute;left:495px;top:212px;width:72px;height:72px;border-radius:50%;background:linear-gradient(160deg,#d8c2a6,#9b7a5c);border:3px solid var(--white)}
.testimonial .who{position:absolute;left:583px;top:228px;color:var(--white)}
.who strong{display:block;font-size:14px;font-weight:700}
.who span{font-size:11px}
.t-dots{position:absolute;left:587px;top:312px;display:flex;gap:5px}
.t-dots i{width:6px;height:6px;border-radius:50%;background:#8fb592}

/* footer */
.footer-brand{position:absolute;left:99px;top:3098px;display:flex;align-items:center;gap:10px}
.footer-brand i{width:16px;height:16px;border-radius:50%;background:var(--orange);flex:none}
.footer-brand span{font-weight:700;font-size:20px;line-height:26px;color:var(--green)}
.f-col{position:absolute;top:3070px}
.f-col h5{font-size:14px;font-weight:700;color:var(--green);margin-bottom:14px}
.f-col li{list-style:none;font-size:11.5px;line-height:22.5px;color:var(--text)}
.f-contact li{font-size:12px;line-height:24px;display:flex;align-items:center;gap:8px}
.social{display:flex;gap:10px;margin-top:14px}
.social i{width:34px;height:34px;border-radius:50%}
.copyright{position:absolute;left:0;top:3271px;width:1200px;height:44px;background:var(--foot-bar);text-align:center;font-size:11.5px;line-height:44px;color:#888}
</style>
</head>
<body>

<header class="site-header">
  <nav class="nav">
    <a class="active" href="#" style="left:117px">Home</a>
    <a href="#" style="left:234px">About Us</a>
    <a href="#" style="left:369px">Services</a>
    <a href="#" style="left:735px">Works</a>
    <a href="#" style="left:853px">Testimonials</a>
    <a href="#" style="left:1009px">Contact us</a>
    <span class="underline"></span>
  </nav>
</header>
<div class="brand-badge"><span>PEBBLEBROOK PLOTS</span></div>

<section class="hero">
  <div class="hero-photo" role="img" aria-label="Suburban house with flowering shrubs and a lawn in front"></div>
  <h1>Garden installation</h1>
  <p>Pick an installation date and pay.</p>
  <a class="btn-solid" href="#">Get an appointment!</a>
  <div class="hero-dots"><i></i><i></i><i></i><i></i></div>
  <svg class="hero-wave" width="1200" height="90" viewBox="0 0 1200 90" aria-hidden="true">
    <path d="M0 40 Q600 110 1200 0 L1200 90 L0 90Z" fill="#8fbf7a"/>
    <path d="M0 50 Q600 115 1200 10 L1200 90 L0 90Z" fill="#2f7a36"/>
    <path d="M0 58 Q600 122 1200 22 L1200 90 L0 90Z" fill="#ffffff"/>
  </svg>
</section>

<h2 class="sec-title" style="top:668px">Welcome to Pebblebrook Plots</h2>
<p class="sec-lead" style="left:220px;top:718px;width:760px">Lorem Ipsum is simply dummy text of the printing and typesetting industry. Lorem Ipsum has been the industry's standard dummy text ever since the 1500</p>

<div class="step" style="left:128px">
  <svg width="120" height="142" viewBox="0 0 120 142" aria-hidden="true">
    <path d="M60 0 C75 30 120 55 120 82 A60 60 0 0 1 0 82 C0 55 45 30 60 0Z" fill="#e4612a"/>
    <g fill="none" stroke="#fff" stroke-width="3">
      <circle cx="60" cy="68" r="14"/><line x1="60" y1="82" x2="60" y2="96"/>
      <path d="M34 96 L86 96 L94 112 L26 112Z"/>
    </g>
  </svg>
  <h3>Step 1</h3>
  <p>Select garden size. Either an 4' X 4', 8' X 4',<br>or 12' X 4'.</p>
</div>
<div class="step" style="left:470px">
  <svg width="120" height="142" viewBox="0 0 120 142" aria-hidden="true">
    <path d="M60 0 C75 30 120 55 120 82 A60 60 0 0 1 0 82 C0 55 45 30 60 0Z" fill="#2f7a36"/>
    <g fill="none" stroke="#fff" stroke-width="3">
      <path d="M34 66 L50 60 L70 66 L86 60 L86 106 L70 112 L50 106 L34 112Z"/>
      <line x1="50" y1="60" x2="50" y2="106"/><line x1="70" y1="66" x2="70" y2="112"/>
      <path d="M60 94 C52 84 50 80 50 76 A10 10 0 0 1 70 76 C70 80 68 84 60 94Z" fill="#2f7a36"/>
    </g>
  </svg>
  <h3>Step 2</h3>
  <p>Select a location. We would like to use online maps to look up a US address, then "drag and drop" one of the garden sizes from step 1 to the location the customer would like us to install the garden at their home.</p>
</div>
<div class="step" style="left:812px">
  <svg width="120" height="142" viewBox="0 0 120 142" aria-hidden="true">
    <path d="M60 0 C75 30 120 55 120 82 A60 60 0 0 1 0 82 C0 55 45 30 60 0Z" fill="#2f7a36"/>
    <g fill="none" stroke="#fff" stroke-width="3">
      <rect x="30" y="66" width="50" height="34" rx="4"/>
      <rect x="40" y="76" width="50" height="34" rx="4" fill="#2f7a36"/>
      <line x1="40" y1="86" x2="90" y2="86"/><line x1="48" y1="100" x2="64" y2="100"/>
    </g>
  </svg>
  <h3>Step 3</h3>
  <p>Pick an installation date and pay. Using an online calendar the customer will pick a date, and then pay for the installation via credit card.</p>
</div>

<section class="band green">
  <h2>Garden installation</h2>
  <p>Lorem Ipsum is simply dummy text of the printing and typesetting industry. Lorem Ipsum has been the industry's standard dummy text ever since the 1500s, when an unknown printer...</p>
  <a class="btn-ghost" href="#">Read more info</a>
</section>
<section class="band orange">
  <h2>Scheduling for installation</h2>
  <p>Lorem Ipsum is simply dummy text of the printing and typesetting industry. Lorem Ipsum has been the industry's standard dummy text ever since the 1500s, when an unknown printer...</p>
  <a class="btn-ghost" href="#">Read more info</a>
</section>
<svg class="band-wave" width="1200" height="130" viewBox="0 0 1200 130" aria-hidden="true">
  <path d="M0 32 Q300 70 600 70 L600 130 L0 130Z" fill="#fff"/>
  <path d="M600 130 Q950 110 1200 0 L1200 130Z" fill="#fff"/>
</svg>

<h2 class="sec-title" style="top:1676px">Recent Works</h2>
<p class="sec-lead" style="left:200px;top:1730px;width:800px">Lorem Ipsum is simply dummy text of the printing and typesetting industry. Lorem Ipsum has been the industry's standard dummy</p>

<svg class="arrow" style="left:62px" width="14" height="26" viewBox="0 0 14 26" aria-hidden="true"><path d="M12 2 L2 13 L12 24" fill="none" stroke="#bbb" stroke-width="2"/></svg>
<div class="work" style="left:99px"><div class="ph" role="img" aria-label="Landscaped lawn with trees and flower beds" style="background:linear-gradient(160deg,#4f7f2e,#8fb84a 60%,#b86a2a)"></div><h4>Lorem ipsum is simply</h4></div>
<div class="work" style="left:356px"><div class="ph" role="img" aria-label="Garden path lined with colourful flower beds" style="background:linear-gradient(160deg,#3c6a2c,#6fa040 55%,#c85a8a)"></div><h4>Lorem ipsum is simply</h4></div>
<div class="work" style="left:612px"><div class="ph" role="img" aria-label="House with a green front lawn" style="background:linear-gradient(180deg,#c9d6e2,#a68e7a 45%,#6e9a45)"></div><h4>Lorem ipsum is simply</h4></div>
<div class="work" style="left:868px"><div class="ph" role="img" aria-label="Carrots growing in dark soil" style="background:linear-gradient(180deg,#7fa84a,#5a3f2a 55%,#3a2a1e)"></div><h4>Lorem ipsum is simply</h4></div>
<svg class="arrow" style="left:1124px" width="14" height="26" viewBox="0 0 14 26" aria-hidden="true"><path d="M2 2 L12 13 L2 24" fill="none" stroke="#bbb" stroke-width="2"/></svg>

<section class="blog">
  <h2 class="sec-title" style="top:42px">Blog Posts</h2>
  <article class="post" style="left:99px">
    <div class="ph" role="img" aria-label="Two women holding a basket of harvested vegetables" style="background:linear-gradient(160deg,#8a9a5a,#6a5a40 55%,#a87a4a)"></div>
    <h4>Lorem Ipsum is simply dummy text of the printing and typesetting</h4>
    <p>Lorem Ipsum is simply dummy text of the printing and typesetting industry. Lorem Ipsum has been the industry's standard dummy text ever since the 1500...</p>
    <a class="btn-solid" href="#">Learn more</a>
  </article>
  <article class="post" style="left:446px">
    <div class="ph" role="img" aria-label="Person planting seedlings in a raised vegetable bed" style="background:linear-gradient(160deg,#3e6e2a,#5f8f34 50%,#4a3a2a)"></div>
    <h4>Lorem Ipsum is simply dummy text of the printing and typesetting</h4>
    <p>Lorem Ipsum is simply dummy text of the printing and typesetting industry. Lorem Ipsum has been the industry's standard dummy text ever since the 1500...</p>
    <a class="btn-solid" href="#">Learn more</a>
  </article>
  <article class="post" style="left:791px">
    <div class="ph" role="img" aria-label="Rolls of fresh turf on prepared soil with a rake" style="background:linear-gradient(180deg,#8a6a4a,#7a5a3a 50%,#4f8a2e 70%,#3f7a26)"></div>
    <h4>Lorem Ipsum is simply dummy text of the printing and typesetting</h4>
    <p>Lorem Ipsum is simply dummy text of the printing and typesetting industry. Lorem Ipsum has been the industry's standard dummy text ever since the 1500...</p>
    <a class="btn-solid" href="#">Learn more</a>
  </article>
</section>

<section class="testimonial">
  <svg class="abs" style="left:0;top:0" width="1200" height="372" viewBox="0 0 1200 372" aria-hidden="true">
    <path d="M0 0 H1200 V330 Q600 338 0 360Z" fill="#2f7a36"/>
    <path d="M0 360 Q600 338 1200 330 V344 Q600 350 0 372Z" fill="#f0a07a"/>
  </svg>
  <svg class="quote-mark" width="40" height="32" viewBox="0 0 40 32" aria-hidden="true">
    <path d="M0 32 V18 Q0 4 14 0 L16 5 Q8 8 8 14 H16 V32Z M22 32 V18 Q22 4 36 0 L38 5 Q30 8 30 14 H38 V32Z" fill="#7fae82"/>
  </svg>
  <blockquote>Lorem Ipsum is simply dummy text of the printing and typesetting industry. Lorem Ipsum has been the industry's standard dummy text ever since the 1500s, when an unknown printer took a galley of type and scrambled it to make a type specimen book</blockquote>
  <div class="avatar" role="img" aria-label="Customer portrait"></div>
  <div class="who"><strong>MARLA QUINLAN</strong><span>- House wife -</span></div>
  <div class="t-dots"><i></i><i></i><i></i></div>
</section>

<footer>
  <div class="footer-brand"><i></i><span>PEBBLEBROOK<br>PLOTS</span></div>
  <div class="f-col f-contact" style="left:347px">
    <h5>Pebblebrook Plots</h5>
    <ul>
      <li>120 Street name, City name,</li>
      <li>Country name : 000000</li>
      <li><svg width="11" height="11" viewBox="0 0 12 12" aria-hidden="true"><path d="M2 1 L5 1 L6 4 L4 5 Q5 7 7 8 L8 6 L11 7 L11 10 Q6 12 2 6 Q0 3 2 1Z" fill="#e4612a"/></svg>(555) 010-2741</li>
      <li><svg width="11" height="9" viewBox="0 0 12 9" aria-hidden="true"><rect width="12" height="9" rx="1" fill="#e4612a"/><path d="M0 1 L6 5 L12 1" fill="none" stroke="#fff" stroke-width="1.2"/></svg>PebblebrookPlots@mailvale.com</li>
    </ul>
  </div>
  <div class="f-col" style="left:617px">
    <h5>Welcome</h5>
    <ul><li>Home</li><li>About Us</li><li>Services</li><li>Products</li><li>Works</li></ul>
  </div>
  <div class="f-col" style="left:765px">
    <h5>Information</h5>
    <ul><li>Terms &amp; Conditions</li><li>Privacy policy</li><li>Disclaimer</li><li>Contact us</li><li>Sitemap</li></ul>
  </div>
  <div class="f-col" style="left:933px">
    <h5>Social media</h5>
    <ul><li>Connect with our social network</li></ul>
    <div class="social"><i style="background:#3b5ea8"></i><i style="background:#39a9e0"></i><i style="background:#d83a2e"></i><i style="background:#1f7aa8"></i></div>
  </div>
  <div class="copyright">Copyright © 2017. Pebblebrook Plots. All rights reserved.</div>
</footer>

</body>
</html>
```